Business Cards - Brightpath Horizon

need to design unique business card for my mortgage business. I need to design credit card style business card for my business or any unique idea that you might have

Target Market(s)

Home Loan customers

Industry/Entity Type

Mortgage Brokerage

Contact Information for Business Card

please design credit card style or very unique style business card

Colors

Designer to choose colors to be used in the design.

Requirements
Must have
• Name
• position
• Phone number
• fax number
• email address
• website address
• social media address
• All above fields will be provided once design in finalised

```html
<!DOCTYPE html>
<html lang="en">
<head>
<meta charset="utf-8">
<title>Brightpath Horizon – Business Cards</title>
<link href="https://fonts.googleapis.com/css2?family=Libre+Baskerville:wght@400;700&display=swap" rel="stylesheet">
<style>
  :root {
    --backdrop: #2b2b2b;
    --brand-blue: #0530c4;
    --brand-orange: #ff8a14;
    --paper: #ffffff;
    --sky: #19a8e8;
  }
  * { margin: 0; padding: 0; box-sizing: border-box; }
  html, body { width: 1200px; height: 960px; overflow: hidden; }
  body {
    background: var(--backdrop);
    position: relative;
    font-family: "Libre Baskerville", Georgia, serif;
  }
  .card {
    position: absolute;
    width: 600px;
    height: 343px;
    border-radius: 20px;
    overflow: hidden;
  }
  .card--front { left: 314px; top: 113px; background: var(--paper); }
  .card--back { left: 311px; top: 472px; background: var(--brand-orange); }

  .brand-name {
    position: absolute;
    line-height: 1;
    font-weight: 400;
  }
  .card--front .brand-name {
    left: 34px; top: 82px;
    color: var(--brand-blue);
  }
  .brand-name__top { display: block; font-size: 22px; letter-spacing: 1px; }
  .brand-name__bottom { display: block; font-size: 42px; margin-top: 4px; }

  .card--back .brand-name {
    left: 0; right: 0; top: 140px;
    text-align: center;
    color: var(--paper);
  }
  .card--back .brand-name__top { font-size: 25px; }
  .card--back .brand-name__bottom { font-size: 50px; }

  .person {
    position: absolute;
    right: 35px; top: 80px;
    text-align: right;
  }
  .person__name { color: var(--brand-blue); font-size: 19px; font-weight: 700; }
  .person__role { color: var(--brand-orange); font-size: 14px; margin-top: 6px; letter-spacing: .3px; }

  .contact-band {
    position: absolute;
    left: 0; top: 212px;
    width: 600px; height: 131px;
    background: var(--brand-blue);
  }
  .contact-list {
    position: absolute;
    left: 34px; top: 32px;
    list-style: none;
    color: var(--paper);
    font-size: 13px;
  }
  .contact-list li { display: flex; align-items: center; height: 19.3px; }
  .contact-list svg { width: 13px; height: 13px; margin-right: 8px; fill: var(--paper); }

  .rooftops {
    position: absolute;
    left: 205px; top: 0;
    width: 395px; height: 131px;
  }

  .social-row {
    position: absolute;
    left: 0; right: 0; top: 280px;
    display: flex; justify-content: center; gap: 3px;
  }
  .social-row span {
    width: 27px; height: 27px;
    border-radius: 50%;
    background: var(--paper);
  }
</style>
</head>
<body>

  <section class="card card--front" aria-label="Business card front">
    <div class="brand-name">
      <span class="brand-name__top">BRIGHTPATH</span>
      <span class="brand-name__bottom">HORIZON</span>
    </div>

    <div class="person">
      <p class="person__name">DANIEL REYES</p>
      <p class="person__role">CEO/FOUNDER</p>
    </div>

    <div class="contact-band">
      <ul class="contact-list">
        <li><svg viewBox="0 0 16 16"><path d="M3 1l3 3-1.5 2a9 9 0 0 0 5.5 5.5L12 10l3 3-2 2C7 15 1 9 1 3z"/></svg>555 214 7730</li>
        <li><svg viewBox="0 0 16 16"><rect x="4" y="1" width="8" height="4"/><rect x="1" y="6" width="14" height="6" rx="1"/><rect x="4" y="10" width="8" height="5"/></svg>555 214 7731</li>
        <li><svg viewBox="0 0 16 16"><path d="M1 4h14v9H1z M1 4l7 5 7-5" fill="none" stroke="#fff" stroke-width="1.6"/></svg>info@brightpath.com</li>
        <li><svg viewBox="0 0 16 16"><circle cx="8" cy="8" r="6.5" fill="none" stroke="#fff" stroke-width="1.6"/><path d="M8 2v12M2 8h12" stroke="#fff" stroke-width="1.2"/></svg>www.brightpath.com</li>
      </ul>

      <svg class="rooftops" viewBox="0 0 395 131" role="img" aria-label="Illustration of white and orange house rooftops">
        <defs>
          <linearGradient id="roofTone" x1="0" y1="0" x2="1" y2="0">
            <stop offset="0" stop-color="#ffffff"/>
            <stop offset="0.6" stop-color="#ffffff"/>
            <stop offset="1" stop-color="#ff8a14"/>
          </linearGradient>
        </defs>
        <polygon points="0,131 140,60 395,20 395,131" fill="url(#roofTone)"/>
      </svg>
    </div>
  </section>

  <section class="card card--back" aria-label="Business card back">
    <div class="brand-name">
      <span class="brand-name__top">BRIGHTPATH</span>
      <span class="brand-name__bottom">HORIZON</span>
    </div>
    <div class="social-row" aria-label="Social media links">
      <span></span><span></span><span></span><span></span>
    </div>
  </section>

</body>
</html>
```